A Health & Fitness Website selling saunas and Cold tubs

www.dockvaultguys.com, www.frostlanterguys, www.chillharborguys
Design a website
We are selling saunas, infrared saunas, cold plunge tubs, and massage chairs to financially successful MEN.
We want professional, simple, masculine with a touch of sexy.
One section for each… saunas, cold plunge tubs, massage chairs.
Each will have at least two buy links to their affiliate/supplier/store.
The landing page / opening page / needs big & bold; a full screen image? a great picture showing the warmth of a sauna? Need your ideas
The pictures are everything.

The Website for our book
https://maebelsvigorguys.com/

Coding

Coded - Design and coding required

Number of Pages Required

1 page

Requirements
Must have
• Great pictures

```html
<!DOCTYPE html>
<html lang="en">
<head>
<meta charset="utf-8">
<title>Maebel Vigor Fitness for Men</title>
<link href="https://fonts.googleapis.com/css2?family=Oswald:wght@500;600;700&family=Poppins:wght@400;500;600&display=swap" rel="stylesheet">
<style>
:root{
  --black:#0b0b0b;
  --ink:#141414;
  --white:#ffffff;
  --grey:#6b6b6b;
  --soft:#f3f3f3;
  --line:#e2e2e2;
  --star:#e2372f;
  --head:'Oswald', 'Arial Narrow', sans-serif;
  --body:'Poppins', Arial, sans-serif;
}
*{box-sizing:border-box;margin:0;padding:0}
html,body{width:1200px;height:5100px;overflow:hidden}
body{position:relative;background:var(--white);font-family:var(--body);color:var(--ink)}
.btn{display:inline-flex;align-items:center;justify-content:center;height:40px;min-width:140px;padding:0 26px;border-radius:20px;font:600 13px/1 var(--body);letter-spacing:.08em;text-transform:uppercase;text-decoration:none}
.btn-outline{background:var(--white);color:var(--ink);border:2px solid var(--ink)}
.btn-solid{background:var(--black);color:var(--white);border:2px solid var(--black)}
.btn-row{display:flex;gap:22px}
.photo{position:absolute}

/* hero */
.hero{position:absolute;left:0;top:0;width:1200px;height:790px;background:var(--black);clip-path:polygon(0 0,100% 0,100% 86%,0 100%);overflow:hidden}
.hero-photo{left:430px;top:0;width:770px;height:790px;background:radial-gradient(ellipse at 60% 45%,#8a7a6c 0%,#4d4540 35%,#1f1c1a 70%,#0b0b0b 100%)}
.hero-fade{position:absolute;left:430px;top:0;width:300px;height:790px;background:linear-gradient(90deg,#0b0b0b,rgba(11,11,11,0))}
.brand{position:absolute;left:40px;top:28px;display:flex;align-items:center;gap:12px}
.brand-dot{width:54px;height:54px;border-radius:50%;border:3px solid var(--white)}
.brand-name{font:600 20px/1.1 var(--head);color:var(--white);text-transform:uppercase;letter-spacing:.04em;width:120px}
.hero-nav{position:absolute;right:80px;top:34px}
.hero-nav .btn-outline{border-color:var(--white)}
.hero-nav .btn-solid{border-color:var(--white)}
.hero-copy{position:absolute;left:64px;top:292px;width:520px;color:var(--white)}
.hero-kicker{font:600 20px/1 var(--head);text-transform:uppercase;letter-spacing:.02em;margin-bottom:12px}
.hero-title{font:700 42px/1.12 var(--head);text-transform:uppercase}
.hero-copy .btn-row{margin-top:40px}

/* intro */
.intro{position:absolute;left:0;top:820px;width:1200px;height:290px}
.intro-photo{left:140px;top:0;width:380px;height:270px;background:linear-gradient(135deg,#d9c3b0 0%,#8e6e5c 45%,#3a2e2a 100%)}
.intro-copy{position:absolute;left:660px;top:36px;width:420px}
.section-title{font:700 36px/1.1 var(--head);text-transform:uppercase}
.intro-copy p{margin:14px 0 26px;font-size:15px;line-height:1.6;color:var(--grey)}

/* circulation */
.circ-photo{left:0;top:1275px;width:1200px;height:360px;background:linear-gradient(100deg,#cfcfcf 0%,#9b948d 30%,#6a625c 60%,#c9c3bc 85%,#e7d9a3 100%)}
.circ-card{position:absolute;left:140px;top:1470px;width:920px;height:270px;background:var(--white);box-shadow:0 10px 30px rgba(0,0,0,.18);display:flex;flex-direction:column;align-items:center;justify-content:center;text-align:center}
.circ-card .section-title{font-size:40px;margin-bottom:30px}

/* benefits */
.benefits{position:absolute;left:0;top:1820px;width:1200px}
.benefits-title{width:820px;margin:0 auto;text-align:center;font:700 30px/1.2 var(--head);text-transform:uppercase}
.benefit-grid{display:grid;grid-template-columns:repeat(5,200px);justify-content:center;row-gap:38px;margin-top:46px}
.benefit{display:flex;flex-direction:column;align-items:center;text-align:center}
.benefit svg{width:110px;height:122px;filter:drop-shadow(0 4px 8px rgba(0,0,0,.14))}
.benefit span{margin-top:12px;font:600 14px/1.2 var(--head);text-transform:uppercase;width:160px}

/* individual */
.individual{position:absolute;left:0;top:2640px;width:1200px;height:380px;background:var(--black);clip-path:polygon(0 12%,100% 0,100% 100%,0 100%);overflow:hidden}
.ind-left{left:0;top:0;width:520px;height:380px;background:linear-gradient(90deg,#6e625b 0%,#3c3532 70%,#0b0b0b 100%)}
.ind-right{left:880px;top:0;width:320px;height:380px;background:linear-gradient(270deg,#b89a7e 0%,#6c5646 55%,#0b0b0b 100%)}
.ind-copy{position:absolute;left:572px;top:110px;color:var(--white)}
.ind-copy .section-title{font-size:34px;width:300px;margin-bottom:26px}
.individual .btn-outline{border-color:var(--white)}
.individual .btn-solid{border-color:var(--white)}

/* reviews */
.reviews{position:absolute;left:0;top:3170px;width:1200px}
.reviews-title{text-align:center;font:700 38px/1 var(--head);text-transform:uppercase}
.review-cols{display:flex;gap:40px;justify-content:center;margin-top:60px;align-items:flex-start}
.review-col{width:290px;display:flex;flex-direction:column;gap:22px}
.review{background:var(--white);box-shadow:0 4px 18px rgba(0,0,0,.12);padding:22px 26px 30px;text-align:center}
.quote{font:700 44px/0.8 Georgia,serif;height:26px}
.stars{color:var(--star);font-size:16px;letter-spacing:3px;margin:6px 0 12px}
.review p{font-size:13.5px;line-height:1.65;color:var(--grey)}
.load-more{display:flex;justify-content:center;margin-top:44px}
.closing{margin-top:40px;text-align:center;font:700 30px/1.15 var(--head);text-transform:uppercase}

/* footer */
.footer{position:absolute;left:0;top:4470px;width:1200px;height:630px;background:var(--black);clip-path:polygon(0 0,100% 14%,100% 100%,0 100%);color:var(--white)}
.footer-brand{position:absolute;left:0;width:1200px;top:130px;display:flex;justify-content:center;align-items:center;gap:14px}
.footer-brand .brand-dot{width:70px;height:70px}
.footer-brand .brand-name{font-size:24px;width:160px}
.contacts{position:absolute;left:0;top:410px;width:1200px;display:flex;justify-content:center;gap:150px}
.contact{display:flex;align-items:center;gap:14px;width:240px}
.contact-icon{width:44px;height:44px;border-radius:50%;background:var(--white);display:flex;align-items:center;justify-content:center;flex:none}
.contact-label{font:600 13px/1 var(--head);text-transform:uppercase;letter-spacing:.08em;margin-bottom:6px}
.contact-text{font-size:12px;color:#cfcfcf}
.footer-bar{position:absolute;left:0;bottom:0;width:1200px;height:62px;border-top:1px solid #2a2a2a;display:flex;align-items:center;justify-content:space-between;padding:0 60px;font-size:12px;color:#bdbdbd}
.social{display:flex;gap:10px}
.social i{width:26px;height:26px;border-radius:50%;border:1.5px solid #bdbdbd}
</style>
</head>
<body>

<header class="hero">
  <div class="photo hero-photo" role="img" aria-label="Athletic man and trainer working out in a dark gym"></div>
  <div class="hero-fade"></div>
  <div class="brand"><span class="brand-dot"></span><span class="brand-name">Maebel Vigor</span></div>
  <nav class="hero-nav btn-row"><a class="btn btn-outline" href="#">Affiliate</a><a class="btn btn-solid" href="#">Store</a></nav>
  <div class="hero-copy">
    <div class="hero-kicker">Maebel Vigor Fitness for Men</div>
    <h1 class="hero-title">Top of the line health products exclusively for the financially successful</h1>
    <div class="btn-row"><a class="btn btn-outline" href="#">Affiliate</a><a class="btn btn-solid" href="#">Store</a></div>
  </div>
</header>

<section class="intro">
  <div class="photo intro-photo" role="img" aria-label="Couple training together on gym equipment"></div>
  <div class="intro-copy">
    <h2 class="section-title">Dramatically improve your health without exercise</h2>
    <p>Successful Men Recognize the Importance of Their Health and Make it a Priority. It's Your Time. You've Earned It.</p>
    <div class="btn-row"><a class="btn btn-outline" href="#">Affiliate</a><a class="btn btn-solid" href="#">Store</a></div>
  </div>
</section>

<div class="photo circ-photo" role="img" aria-label="Man and woman resting between sets in a bright gym"></div>
<section class="circ-card">
  <h2 class="section-title">A man's body thrives on circulation<br>and it doesn't care how you get it</h2>
  <div class="btn-row"><a class="btn btn-outline" href="#">Affiliate</a><a class="btn btn-solid" href="#">Store</a></div>
</section>

<section class="benefits">
  <h2 class="benefits-title">When there's no time for exercise. Use hot, cold, or massage. The benefits are numerous.</h2>
  <div class="benefit-grid">
    <div class="benefit"><svg viewBox="0 0 110 122"><polygon points="55,2 107,31 107,91 55,120 3,91 3,31" fill="#fff"/><circle cx="55" cy="61" r="16" fill="none" stroke="#111" stroke-width="2.5"/><path d="M48 64q7 6 14 0" fill="none" stroke="#111" stroke-width="2.5"/></svg><span>Relieve stress</span></div>
    <div class="benefit"><svg viewBox="0 0 110 122"><polygon points="55,2 107,31 107,91 55,120 3,91 3,31" fill="#fff"/><path d="M55 44q-14 18-14 26a14 14 0 0 0 28 0q0-8-14-26z" fill="none" stroke="#111" stroke-width="2.5"/></svg><span>Detox your pores</span></div>
    <div class="benefit"><svg viewBox="0 0 110 122"><polygon points="55,2 107,31 107,91 55,120 3,91 3,31" fill="#fff"/><path d="M62 44a18 18 0 1 0 10 28a14 14 0 0 1-10-28z" fill="none" stroke="#111" stroke-width="2.5"/></svg><span>Sleep better</span></div>
    <div class="benefit"><svg viewBox="0 0 110 122"><polygon points="55,2 107,31 107,91 55,120 3,91 3,31" fill="#fff"/><rect x="40" y="46" width="30" height="30" rx="6" fill="none" stroke="#111" stroke-width="2.5"/><path d="M47 61h16M55 53v16" stroke="#111" stroke-width="2.5"/></svg><span>Healthier skin</span></div>
    <div class="benefit"><svg viewBox="0 0 110 122"><polygon points="55,2 107,31 107,91 55,120 3,91 3,31" fill="#fff"/><path d="M36 70q10-22 24-12q10 8 14-6" fill="none" stroke="#111" stroke-width="2.5"/></svg><span>Relieve muscle tension</span></div>
    <div class="benefit"><svg viewBox="0 0 110 122"><polygon points="55,2 107,31 107,91 55,120 3,91 3,31" fill="#fff"/><path d="M58 42l-14 22h11l-3 17l14-23h-11z" fill="none" stroke="#111" stroke-width="2.5"/></svg><span>Boost energy levels</span></div>
    <div class="benefit"><svg viewBox="0 0 110 122"><polygon points="55,2 107,31 107,91 55,120 3,91 3,31" fill="#fff"/><path d="M38 78l18-18l8 8l12-16M68 52h8v8" fill="none" stroke="#111" stroke-width="2.5"/></svg><span>Increase testosterone</span></div>
    <div class="benefit"><svg viewBox="0 0 110 122"><polygon points="55,2 107,31 107,91 55,120 3,91 3,31" fill="#fff"/><circle cx="55" cy="61" r="15" fill="none" stroke="#111" stroke-width="2.5"/><path d="M45 61h20" stroke="#111" stroke-width="2.5"/></svg><span>Reduce inflammation</span></div>
    <div class="benefit"><svg viewBox="0 0 110 122"><polygon points="55,2 107,31 107,91 55,120 3,91 3,31" fill="#fff"/><path d="M55 42l16 6v12q0 14-16 20q-16-6-16-20v-12z" fill="none" stroke="#111" stroke-width="2.5"/></svg><span>Increase immunity</span></div>
    <div class="benefit"><svg viewBox="0 0 110 122"><polygon points="55,2 107,31 107,91 55,120 3,91 3,31" fill="#fff"/><circle cx="55" cy="61" r="16" fill="none" stroke="#111" stroke-width="2.5"/><path d="M48 58q7-6 14 0" fill="none" stroke="#111" stroke-width="2.5"/></svg><span>Reduce depression</span></div>
    <div class="benefit"><svg viewBox="0 0 110 122"><polygon points="55,2 107,31 107,91 55,120 3,91 3,31" fill="#fff"/><path d="M48 42v16M62 80v-16" stroke="#111" stroke-width="2.5"/><circle cx="55" cy="61" r="7" fill="none" stroke="#111" stroke-width="2.5"/></svg><span>Alleviate joint pain</span></div>
    <div class="benefit"><svg viewBox="0 0 110 122"><polygon points="55,2 107,31 107,91 55,120 3,91 3,31" fill="#fff"/><path d="M55 78l-16-16a9 9 0 0 1 16-12a9 9 0 0 1 16 12z" fill="none" stroke="#111" stroke-width="2.5"/></svg><span>Lower the risk of cardiovascular disease</span></div>
    <div class="benefit"><svg viewBox="0 0 110 122"><polygon points="55,2 107,31 107,91 55,120 3,91 3,31" fill="#fff"/><path d="M55 42q-12 12-10 24a10 10 0 0 0 20 0q0-8-6-12q0 8-4 8q2-10 0-20z" fill="none" stroke="#111" stroke-width="2.5"/></svg><span>Increase metabolism promote weight loss</span></div>
    <div class="benefit"><svg viewBox="0 0 110 122"><polygon points="55,2 107,31 107,91 55,120 3,91 3,31" fill="#fff"/><rect x="39" y="45" width="32" height="32" rx="4" fill="none" stroke="#111" stroke-width="2.5"/><path d="M47 56q8-6 16 0" fill="none" stroke="#111" stroke-width="2.5"/></svg><span>Promote weight loss</span></div>
    <div class="benefit"><svg viewBox="0 0 110 122"><polygon points="55,2 107,31 107,91 55,120 3,91 3,31" fill="#fff"/><circle cx="55" cy="61" r="16" fill="none" stroke="#111" stroke-width="2.5"/><path d="M55 51v10l7 5" fill="none" stroke="#111" stroke-width="2.5"/></svg><span>A longer &amp; healthier life</span></div>
  </div>
</section>

<section class="individual">
  <div class="photo ind-left" role="img" aria-label="Man lifting dumbbells with a training partner"></div>
  <div class="photo ind-right" role="img" aria-label="Woman in workout wear standing in the gym"></div>
  <div class="ind-copy">
    <h2 class="section-title">Specific improvements will be individual to you</h2>
    <div class="btn-row"><a class="btn btn-outline" href="#">Affiliate</a><a class="btn btn-solid" href="#">Store</a></div>
  </div>
</section>

<section class="reviews">
  <h2 class="reviews-title">Customer Reviews</h2>
  <div class="review-cols">
    <div class="review-col">
      <article class="review"><div class="quote">&ldquo;</div><div class="stars">★★★★★</div><p>I sit in my sauna every morning for ten minutes before I take a shower and head off to work. It's the only thing I found that really wakes me up. I'm not a coffee drinker so this is now the perfect start to my day.</p></article>
      <article class="review"><div class="quote">&ldquo;</div><div class="stars">★★★★★</div><p>I've always loved a good sweat. It just feels so rejuvenating. I guess I relate it to when I was younger and got a good sweat through exercise. A nice shower to rinse it all away and I feel like a new person.</p></article>
      <article class="review"><div class="quote">&ldquo;</div><div class="stars">★★★★★</div><p>Having a sauna in my home has been a game changer. After a long day at work I step into the warmth and it's total relaxation. The heat and gentle steam instantly melt me. It's like a mini vacation without leaving home.</p></article>
    </div>
    <div class="review-col">
      <article class="review"><div class="quote">&ldquo;</div><div class="stars">★★★★★</div><p>I tried to take the cold plunge after a hard week. My body ached and I wasn't sure I could handle it. Three minutes later the inflammation was gone and my head was clear. It has been a life changing relief.</p></article>
      <article class="review"><div class="quote">&ldquo;</div><div class="stars">★★★★★</div><p>We're your typical old married couple. After thirty years the spark had faded. I had been using my cold plunge for about two months, every morning, and my wife noticed the change in my energy right away. Now we're out dancing again.</p></article>
      <article class="review"><div class="quote">&ldquo;</div><div class="stars">★★★★★</div><p>I pretty much spend my life at the office. There's no time to use a cold tub or a sauna. I love the space at home for a massage chair and it's heaven. I have fallen asleep and spent more than one night in that chair.</p></article>
    </div>
    <div class="review-col">
      <article class="review"><div class="quote">&ldquo;</div><div class="stars">★★★★★</div><p>I love a good massage but making an appointment is almost impossible with my schedule. The chair is always there. I climb in and let it do its thing. I forget about work so much that it usually turns in to a power nap.</p></article>
      <article class="review"><div class="quote">&ldquo;</div><div class="stars">★★★★★</div><p>My massage chair has been a life saver. Having back pain for years, the chair gives me the relief I need. I can dial in for a deep massage or gentle pressure. I would never be able to get a daily massage any other way.</p></article>
      <article class="review"><div class="quote">&ldquo;</div><div class="stars">★★★★★</div><p>Before my massage chair I walked like an old man. I didn't walk much and sat way too much. I'm only fifty. That is not old. I knew I needed to move but it was just too uncomfortable. Every step took effort. Now I spend twenty minutes in the chair and feel energized.</p></article>
    </div>
  </div>
  <div class="load-more"><a class="btn btn-solid" href="#">Load More</a></div>
  <h2 class="closing">Everything works better with<br>increased blood flow</h2>
</section>

<footer class="footer">
  <div class="footer-brand"><span class="brand-dot"></span><span class="brand-name">Maebel Vigor</span></div>
  <div class="contacts">
    <div class="contact">
      <span class="contact-icon"><svg width="20" height="16" viewBox="0 0 20 16"><rect x="1" y="1" width="18" height="14" rx="2" fill="none" stroke="#111" stroke-width="2"/><path d="M1 2l9 7l9-7" fill="none" stroke="#111" stroke-width="2"/></svg></span>
      <div><div class="contact-label">Email</div><div class="contact-text">info@maebelvigor.com</div></div>
    </div>
    <div class="contact">
      <span class="contact-icon"><svg width="16" height="20" viewBox="0 0 16 20"><path d="M8 19s7-7 7-11A7 7 0 0 0 1 8c0 4 7 11 7 11z" fill="none" stroke="#111" stroke-width="2"/><circle cx="8" cy="8" r="2.5" fill="#111"/></svg></span>
      <div><div class="contact-label">Address</div><div class="contact-text">123 st anon all state random</div></div>
    </div>
    <div class="contact">
      <span class="contact-icon"><svg width="18" height="18" viewBox="0 0 18 18"><path d="M4 1l3 4l-2 2q2 4 6 6l2-2l4 3l-2 3Q7 16 1 3z" fill="none" stroke="#111" stroke-width="2" stroke-linejoin="round"/></svg></span>
      <div><div class="contact-label">Phone</div><div class="contact-text">123-456-7890</div></div>
    </div>
  </div>
  <div class="footer-bar">
    <span>© 2024 Maebel Vigor Fitness. All Rights Reserved.</span>
    <span class="social"><i></i><i></i><i></i><i></i></span>
  </div>
</footer>

</body>
</html>
```